Stationary Set Rebrand for Brennick

We are a Canadian Distribution and Service Company that was established in 1969. Over the past 5 decades we have expanded our business and have warehouses across Canada. We specialize in adhesive tapes, adhesives, films, safety, warehouse, shipping, janitorial and packaging supplies.

We have updated our logo design and would like a new corporate branding identity that includes a new fresh Stationary Set (Business Cards, Letterhead, Letterhead MS Word, Envelope, Presentation Folders, Email Signatures, Notepad Covers, etc.)

Target Market(s)

Industrial Business Sector

Font styles to use
Sans Serif

Colors
0054AA
0677BA
7BADD7
CADEEF
E8F1F8
0094D4
00A9DD
6FCCEA
C7EBF8
E9F6FB
00AB8E
00BBA5
67D7C9
C6EFE9
E9F9F6
EB3D1F
EC4F4E
F09395
F8D3D4
FCEDEE

Requirements
Should not have
• Colors not too light, darker colours preferred

```html
<!DOCTYPE html>
<html lang="en">
<head>
<meta charset="utf-8">
<title>Brennick Business Card</title>
<link rel="stylesheet" href="https://fonts.googleapis.com/css2?family=Poppins:wght@400;500;600;800&family=Oswald:wght@600&display=swap">
<style>
  :root {
    --board: #f0f0f0;
    --card: #ffffff;
    --ink: #000000;
    --text: #1a1a1a;
    --red: #d71920;
    --shadow: rgba(0, 0, 0, 0.35);
  }
  * { margin: 0; padding: 0; box-sizing: border-box; }
  html, body { width: 1200px; height: 987px; overflow: hidden; }
  body {
    background: var(--board);
    position: relative;
    font-family: "Poppins", sans-serif;
    color: var(--text);
  }
  .card {
    position: absolute;
    left: 245px;
    width: 710px;
    height: 405px;
    background: var(--card);
    border-radius: 34px;
    overflow: hidden;
    box-shadow: 0 14px 26px var(--shadow), -6px 4px 18px rgba(0,0,0,0.18);
  }
  .card--front { top: 68px; }
  .card--back { top: 514px; }

  .card__band {
    position: absolute;
    left: 0; bottom: 0;
    width: 710px; height: 26px;
  }

  .brand {
    position: absolute;
    left: 0; right: 0;
    text-align: center;
  }
  .brand__name {
    display: inline-flex;
    align-items: center;
    gap: 12px;
    font-weight: 800;
    color: var(--ink);
    line-height: 1;
    letter-spacing: -1px;
  }
  .brand__dot {
    display: inline-block;
    border-radius: 50%;
    background: var(--red);
  }
  .brand__tagline {
    font-weight: 600;
    color: var(--ink);
  }

  .card--front .brand { top: 128px; }
  .card--front .brand__name { font-size: 96px; }
  .card--front .brand__dot { width: 22px; height: 22px; }
  .card--front .brand__tagline { font-size: 24px; margin-top: 6px; }

  .card--back .brand { top: 32px; }
  .card--back .brand__name { font-size: 56px; gap: 8px; }
  .card--back .brand__dot { width: 14px; height: 14px; }
  .card--back .brand__tagline { font-size: 15px; margin-top: 2px; }

  .person {
    position: absolute;
    right: 400px;
    top: 224px;
    text-align: right;
  }
  .person__name {
    font-size: 39px;
    line-height: 1.1;
    font-weight: 400;
    color: var(--ink);
    letter-spacing: 1px;
    white-space: nowrap;
  }
  .person__first { color: var(--red); font-weight: 600; }
  .person__role {
    font-size: 18px;
    font-weight: 500;
    color: var(--ink);
    letter-spacing: 0.5px;
    margin-top: 2px;
  }

  .divider {
    position: absolute;
    left: 355px;
    top: 204px;
    width: 1px;
    height: 117px;
    background: var(--red);
  }

  .contacts {
    position: absolute;
    left: 397px;
    top: 206px;
    list-style: none;
  }
  .contacts__item {
    display: flex;
    align-items: center;
    gap: 9px;
    height: 26.5px;
    font-size: 20px;
    color: var(--ink);
    letter-spacing: 0.3px;
  }
  .contacts__icon { width: 16px; height: 16px; flex: none; }

  .address {
    position: absolute;
    left: 0; right: 0;
    top: 338px;
    text-align: center;
    font-size: 18.5px;
    color: var(--ink);
    letter-spacing: 0.3px;
  }

  .version-label {
    position: absolute;
    left: 977px;
    top: 448px;
    font-family: "Oswald", sans-serif;
    font-weight: 600;
    font-size: 62px;
    color: var(--ink);
    line-height: 1;
  }
</style>
</head>
<body>

  <section class="card card--front">
    <div class="brand">
      <div class="brand__name">Brennick<span class="brand__dot"></span></div>
      <div class="brand__tagline">Tape and Packaging Specialists</div>
    </div>
    <svg class="card__band" viewBox="0 0 710 26" aria-hidden="true">
      <polygon points="0,0 316,0 354,26 0,26" fill="var(--ink)"/>
      <polygon points="342,0 710,0 710,26 380,26" fill="var(--red)"/>
    </svg>
  </section>

  <section class="card card--back">
    <div class="brand">
      <div class="brand__name">Brennick<span class="brand__dot"></span></div>
      <div class="brand__tagline">Tape and Packaging Specialists</div>
    </div>

    <div class="person">
      <div class="person__name"><span class="person__first">Maren</span> Dolask</div>
      <div class="person__role">Founder &amp; CEO</div>
    </div>

    <div class="divider"></div>

    <ul class="contacts">
      <li class="contacts__item">
        <svg class="contacts__icon" viewBox="0 0 16 16" aria-hidden="true">
          <rect x="4" y="1" width="8" height="14" rx="1.5" fill="none" stroke="var(--red)" stroke-width="1.4"/>
          <circle cx="8" cy="12.6" r="0.8" fill="var(--red)"/>
        </svg>
        (555) 214-3086
      </li>
      <li class="contacts__item">
        <svg class="contacts__icon" viewBox="0 0 16 16" aria-hidden="true">
          <path d="M3 1.5 L6 4.5 L4.6 6.4 C5.6 8.4 7.6 10.4 9.6 11.4 L11.5 10 L14.5 13 L12.6 14.8 C7 14 2 9 1.2 3.4 Z" fill="var(--red)"/>
          <path d="M9 2.5 A4.5 4.5 0 0 1 13.5 7" fill="none" stroke="var(--red)" stroke-width="1.2"/>
          <path d="M9 5 A2 2 0 0 1 11 7" fill="none" stroke="var(--red)" stroke-width="1.2"/>
        </svg>
        (555) 214-3190
      </li>
      <li class="contacts__item">
        <svg class="contacts__icon" viewBox="0 0 16 16" aria-hidden="true">
          <circle cx="8" cy="8" r="7" fill="var(--red)"/>
          <ellipse cx="8" cy="8" rx="3" ry="7" fill="none" stroke="#fff" stroke-width="1"/>
          <line x1="1" y1="8" x2="15" y2="8" stroke="#fff" stroke-width="1"/>
        </svg>
        info@yourwebsite.com
      </li>
      <li class="contacts__item">
        <svg class="contacts__icon" viewBox="0 0 16 16" aria-hidden="true">
          <rect x="1" y="3.5" width="14" height="10" rx="1" fill="var(--red)"/>
          <path d="M1.5 4 L8 9 L14.5 4" fill="none" stroke="#fff" stroke-width="1.1"/>
        </svg>
        www.yourwebsite.com
      </li>
    </ul>

    <p class="address">418 Harbourline Rd. Unit 12 Kingsford, ON K7P 2R4</p>

    <svg class="card__band" viewBox="0 0 710 26" aria-hidden="true">
      <polygon points="0,0 316,0 354,26 0,26" fill="var(--ink)"/>
      <polygon points="342,0 710,0 710,26 380,26" fill="var(--red)"/>
    </svg>
  </section>

  <div class="version-label">Version-3</div>

</body>
</html>
```